Tolvik Commercial Cleaning is lookong for a new business card design.

A fresh new design that's professional and stylish. We need a serious upgrade to our business cards. I have included pictures of our existing ones. Our clients include professional individuals and business owners. We woupdblike something professional and upbeat. Please have fun and see what you come uo with.

Target Market(s)

Property managers, business owners, facility managers and other similar professionals

Industry/Entity Type

Janitorial

Contact Information for Business Card

Name, cell, office number, email, web address

Font styles to use
Sans Serif

Colors

Designer to choose colors to be used in the design.

Requirements
Must have
• please use the green color in our logo
Nice to have
• Bar code
Should not have
• Address

```html
<!DOCTYPE html>
<html lang="en">
<head>
<meta charset="utf-8">
<title>Tolvik Commercial Cleaning – Business Card</title>
<link href="https://fonts.googleapis.com/css2?family=Montserrat:wght@400;500;700&display=swap" rel="stylesheet">
<style>
  :root {
    --page: #ece8e2;
    --card-white: #ffffff;
    --brand-green: #41ad5a;
    --brand-green-deep: #2f8f47;
    --ink: #2a2a2a;
    --shadow: rgba(0, 0, 0, 0.45);
  }
  * { margin: 0; padding: 0; box-sizing: border-box; }
  html, body {
    width: 900px;
    height: 1200px;
    overflow: hidden;
    background: var(--page);
    font-family: "Montserrat", Arial, sans-serif;
  }
  .canvas { position: relative; width: 900px; height: 1200px; }
  .card {
    position: absolute;
    left: 80px;
    width: 742px;
    height: 440px;
    border-radius: 32px;
    box-shadow: 4px 6px 10px var(--shadow);
  }
  .card--front { top: 132px; background: var(--card-white); }
  .card--back { top: 638px; background: var(--brand-green); }

  .wordmark {
    position: absolute;
    left: 0;
    width: 100%;
    text-align: center;
    font-weight: 700;
    font-size: 42px;
    letter-spacing: -0.5px;
    white-space: nowrap;
  }
  .card--front .wordmark { top: 152px; color: var(--brand-green); }
  .card--back .wordmark { top: 176px; color: var(--brand-green-deep); }

  .holder {
    position: absolute;
    right: 410px;
    top: 322px;
    text-align: right;
  }
  .holder__name {
    font-weight: 700;
    font-size: 25px;
    color: var(--brand-green);
    line-height: 32px;
  }
  .holder__title {
    font-size: 15px;
    color: var(--ink);
    line-height: 22px;
  }
  .divider {
    position: absolute;
    left: 353px;
    top: 318px;
    width: 2px;
    height: 60px;
    background: var(--brand-green);
  }
  .contact {
    position: absolute;
    left: 376px;
    top: 314px;
    list-style: none;
  }
  .contact__item {
    display: flex;
    align-items: center;
    height: 22px;
    font-size: 16px;
    color: var(--ink);
  }
  .contact__icon {
    width: 13px;
    height: 13px;
    margin-right: 14px;
    fill: var(--brand-green);
    flex: none;
  }
</style>
</head>
<body>
<div class="canvas">
  <section class="card card--front">
    <div class="wordmark">Tolvik Commercial Cleaning</div>

    <div class="holder">
      <div class="holder__name">Mara Lindqvist</div>
      <div class="holder__title">CEO &amp; Founder</div>
    </div>
    <div class="divider"></div>

    <ul class="contact">
      <li class="contact__item">
        <svg class="contact__icon" viewBox="0 0 16 16" aria-hidden="true"><path d="M1 5c0-2 3-3 7-3s7 1 7 3v1.5h-3.5V5h-7v1.5H1z"/><path d="M3 8h10l1.5 6h-13z"/></svg>
        (37) 555-0187
      </li>
      <li class="contact__item">
        <svg class="contact__icon" viewBox="0 0 16 16" aria-hidden="true"><path d="M1 4h14v1L8 9.5 1 5z"/><path d="M1 6.5l7 4.5 7-4.5V13H1z"/></svg>
        mara@tolvikcleaning.com
      </li>
      <li class="contact__item">
        <svg class="contact__icon" viewBox="0 0 16 16" aria-hidden="true"><circle cx="8" cy="8" r="7"/><path d="M4 4.5c1.5 0 2 1 3 1s1 1.5 0 2-2 1-1.5 2.5S4 12 3 10" fill="#fff"/><path d="M10 3.5c1 .5 1 1.5 2 2s.5 2-.5 2.5-1 2 .5 2.5" fill="#fff"/></svg>
        www.tolvikcleaning.com
      </li>
    </ul>
  </section>

  <section class="card card--back">
    <div class="wordmark">Tolvik Commercial Cleaning</div>
  </section>
</div>
</body>
</html>
```